Resposive web site in 4 languages + image gallery + logo design

We need a web page, which will work on all devices.
I have uploaded web page concept.
Company name: Praxelun
Industry/Entity Type
It Company
Logo Text
quality matters
Coding
Coded - Design and coding required
Number of Pages Required
1 page

```html
<!DOCTYPE html>
<html lang="en">
<head>
<meta charset="utf-8">
<title>Praxelun – Woodworks, Stoneworks, Restoration</title>
<link href="https://fonts.googleapis.com/css2?family=Open+Sans:wght@400;600;700;800&display=swap" rel="stylesheet">
<style>
:root{
  --orange:#e07f1f;
  --brown:#4a1c0a;
  --text:#3a3a3a;
  --muted:#555;
  --page:#f4f4f4;
  --card:#ffffff;
  --line:#e3e3e3;
  --bar:#111;
  --white:#fff;
}
*{box-sizing:border-box;margin:0;padding:0}
html,body{width:698px;height:1200px;overflow:hidden}
body{position:relative;background:var(--page);font-family:"Open Sans",Arial,sans-serif;color:var(--text)}
.abs{position:absolute}

/* hero */
.hero{left:0;top:0;width:698px;height:344px;overflow:hidden;
  background:radial-gradient(ellipse at 62% 45%,#8a6a4a 0%,#5a4028 35%,#2e2016 75%,#1c140e 100%)}
.hero-shade{inset:0;background:linear-gradient(90deg,rgba(0,0,0,.45) 0%,rgba(0,0,0,.15) 60%,rgba(0,0,0,.25) 100%)}
.brand{left:94px;top:16px;color:var(--white);font-weight:800;font-size:19px;letter-spacing:.5px}
.nav{top:21px;color:var(--white);font-size:6.5px;font-weight:600;text-transform:uppercase;display:flex;align-items:center;gap:3px}
.lang-dot{width:12px;height:12px;border-radius:50%;background:#c8102e;border:1.5px solid #fff}
.social-dot{width:12px;height:12px;border-radius:50%;border:1px solid #fff}
.hero-title{left:94px;top:154px;color:var(--white);font-size:22px;font-weight:400;letter-spacing:.3px}
.hero-sub{left:94px;top:188px;color:var(--white);font-size:10.2px;line-height:14.4px}
.btn{left:94px;top:226px;width:112px;height:20px;background:var(--orange);color:var(--white);
  font-size:7.3px;font-weight:700;text-transform:uppercase;display:flex;align-items:center;justify-content:center}
.slide-arrow{top:206px;width:20px;height:20px;border-radius:50%;border:1px solid rgba(255,255,255,.6)}

/* services */
.section-title{color:var(--brown);font-weight:700;font-size:12.2px;text-transform:uppercase}
.card{left:94px;width:510px;height:134px;background:var(--card);border:1px solid var(--line)}
.card-photo{left:10px;top:13px;width:146px;height:110px}
.ph-arrow{width:12px;height:16px;background:rgba(0,0,0,.55)}
.card-title{left:166px;top:18px;color:var(--orange);font-weight:700;font-size:8px;text-transform:uppercase}
.card-text{left:166px;top:36px;width:326px;font-size:6.1px;line-height:11.2px;color:var(--text)}
.tags{left:166px;top:101px;display:flex;gap:9px;font-size:5.6px;font-weight:700;text-transform:uppercase;color:#444}
.tags span{display:flex;align-items:center;gap:2px}
.tags span:first-child{color:var(--orange)}
.tags svg{width:7px;height:7px}

/* about */
.about{left:0;top:834px;width:698px;height:160px;background:var(--white)}
.about-photo{left:94px;top:41px;width:168px;height:102px;background:linear-gradient(135deg,#8a8f96 0%,#b08a5a 45%,#6a4a2c 100%)}
.about-body{left:277px;top:42px;width:330px;display:flex;flex-direction:column}
.about-text{font-size:7.1px;line-height:13.2px;color:var(--muted)}
.quality{margin-top:8px;color:var(--orange);font-weight:600;font-size:8.3px;line-height:12px}
.sign{margin-top:3px;font-size:7.2px;color:var(--muted)}

/* footer */
.footer{left:0;top:994px;width:698px;height:174px;background:linear-gradient(180deg,#2a201a 0%,#1d1612 60%,#241b15 100%)}
.foot-title{color:var(--white);font-weight:700;font-size:11.6px;text-transform:uppercase}
.addr{left:94px;top:55px;color:#e6e6e6;font-size:6.2px;line-height:11.8px}
.addr div{display:flex;align-items:center;gap:5px}
.addr svg{width:6px;height:6px;fill:#e6e6e6}
.circles{left:95px;top:110px;display:flex;gap:4px}
.circles i{width:15px;height:15px;border:1px solid #eee;border-radius:50%}
.field{background:#050505;border:1px solid #3a3a3a;color:#ddd;font-size:6.3px;padding:7px 8px}
.send{left:556px;top:1115px;width:48px;height:21px;background:var(--orange);color:var(--white);font-size:7.5px;font-weight:700;display:flex;align-items:center;justify-content:center;gap:3px}
.bottom{left:0;top:1168px;width:698px;height:32px;background:var(--bar);color:#ddd;font-size:5.8px;display:flex;align-items:center;justify-content:center}
</style>
</head>
<body>

<header class="abs hero">
  <div class="abs" style="inset:0" role="img" aria-label="Photo of a carpenter's hands planing a wooden board among wood shavings"></div>
  <div class="abs hero-shade"></div>
  <div class="abs brand">PRAXELUN</div>
  <nav>
    <div class="abs nav" style="left:362px">Services</div>
    <div class="abs nav" style="left:413px">About us</div>
    <div class="abs nav" style="left:468px">Contact</div>
    <div class="abs nav" style="left:515px;top:18px"><span class="lang-dot"></span>Eng ▾</div>
    <div class="abs nav" style="left:556px;top:18px"><span class="social-dot"></span>Social</div>
  </nav>
  <h1 class="abs hero-title">WOODWORKS</h1>
  <p class="abs hero-sub">Lorem ipsum dolor sit amet, consectetur adipiscing elit,<br>sed do eiusmod tempor incididunt ut laborelo</p>
  <a class="abs btn">Get started here</a>
  <svg class="abs slide-arrow" style="left:16px" viewBox="0 0 20 20"><path d="M11 6l-4 4 4 4" stroke="#fff" fill="none" stroke-width="1"/></svg>
  <svg class="abs slide-arrow" style="left:663px" viewBox="0 0 20 20"><path d="M9 6l4 4-4 4" stroke="#fff" fill="none" stroke-width="1"/></svg>
</header>

<h2 class="abs section-title" style="left:0;width:698px;text-align:center;top:357px">Our services</h2>

<article class="abs card" style="top:385px">
  <div class="abs card-photo" role="img" aria-label="Photo of craftsmen working on wooden planks in a workshop" style="background:linear-gradient(135deg,#c9c3bb 0%,#a8876a 55%,#7a5a3e 100%)"></div>
  <div class="abs ph-arrow" style="left:10px;top:61px"></div><div class="abs ph-arrow" style="left:144px;top:61px"></div>
  <h3 class="abs card-title">Woodworks</h3>
  <p class="abs card-text">Timber is, in essence, a natural and warm material. Wood is also relatively durable and easy to work with, which has made it a favourite of builders throughout history. Our goal is to offer suitable products and quality furniture with installation and after-sales service to all of our clients. In order to achieve this, we're ready to help our clients in all stages of construction from design to production and maintenance.</p>
  <div class="abs tags">
    <span><svg viewBox="0 0 8 8"><rect x="0" y="3" width="8" height="4" fill="var(--orange)"/></svg>Furniture</span>
    <span><svg viewBox="0 0 8 8"><rect width="8" height="8" fill="#555"/></svg>Windows</span>
    <span><svg viewBox="0 0 8 8"><rect x="1" width="6" height="8" fill="none" stroke="#555"/></svg>Doors</span>
    <span><svg viewBox="0 0 8 8"><path d="M0 8h3V5h2V2h3" stroke="#555" fill="none"/></svg>Staircases</span>
    <span><svg viewBox="0 0 8 8"><path d="M0 7V3l4-2 4 2v4" stroke="#555" fill="none"/></svg>Woodcarving</span>
    <span><svg viewBox="0 0 8 8"><circle cx="4" cy="4" r="3" fill="#555"/></svg>Graining</span>
  </div>
</article>

<article class="abs card" style="top:529px">
  <div class="abs card-photo" role="img" aria-label="Photo of hands laying natural stone on a wall" style="background:linear-gradient(135deg,#6e6e6e 0%,#a9a9a9 50%,#777 100%)"></div>
  <div class="abs ph-arrow" style="left:10px;top:61px"></div><div class="abs ph-arrow" style="left:144px;top:61px"></div>
  <h3 class="abs card-title">Stoneworks</h3>
  <p class="abs card-text">The natural stone found in the ground has been used in construction for centuries because of its durability.<br>A structure built by a skilled craftsman from natural stone is unique, genuine and durable, and perfect for our bracing climate. Our experienced craftsmen are ready to help you in all stages of construction from planning to completion.</p>
  <div class="abs tags" style="gap:7px">
    <span><svg viewBox="0 0 8 8"><rect y="2" width="8" height="5" fill="var(--orange)"/></svg>Walls</span>
    <span><svg viewBox="0 0 8 8"><rect x="2" width="4" height="8" fill="#555"/></svg>Terraces</span>
    <span><svg viewBox="0 0 8 8"><ellipse cx="4" cy="5" rx="4" ry="2" fill="#555"/></svg>Paths</span>
    <span><svg viewBox="0 0 8 8"><path d="M0 7l2-5h4l2 5z" fill="#555"/></svg>Outdoor kitchens</span>
    <span><svg viewBox="0 0 8 8"><rect y="2" width="8" height="6" fill="#555"/></svg>Fireplaces</span>
    <span><svg viewBox="0 0 8 8"><path d="M2 0v8h5" stroke="#555" fill="none"/></svg>Smokeries</span>
    <span><svg viewBox="0 0 8 8"><path d="M0 3h8M0 5h8" stroke="#555"/></svg>Fences</span>
  </div>
</article>

<article class="abs card" style="top:674px">
  <div class="abs card-photo" role="img" aria-label="Photo of a hand restoring an old wooden surface" style="background:linear-gradient(135deg,#3a1c0e 0%,#b06a3e 50%,#5a2a14 100%)"></div>
  <div class="abs ph-arrow" style="left:10px;top:61px"></div><div class="abs ph-arrow" style="left:144px;top:61px"></div>
  <h3 class="abs card-title">Restoration</h3>
  <p class="abs card-text">It's good to see that fixing old things has become popular again in recent years and people are trying to find ways to preserve valuable old windows and pieces of furniture before deciding to replace them. It is possible to give a new life to almost any wooden door, window, piece of furniture or staircase. The extensive experience of our craftsmen will help you achieve the desired result.</p>
  <div class="abs tags">
    <span><svg viewBox="0 0 8 8"><rect x="0" y="3" width="8" height="4" fill="var(--orange)"/></svg>Furniture</span>
    <span><svg viewBox="0 0 8 8"><rect width="8" height="8" fill="#555"/></svg>Windows</span>
    <span><svg viewBox="0 0 8 8"><rect x="1" width="6" height="8" fill="none" stroke="#555"/></svg>Doors</span>
    <span><svg viewBox="0 0 8 8"><path d="M0 8h3V5h2V2h3" stroke="#555" fill="none"/></svg>Staircases</span>
    <span><svg viewBox="0 0 8 8"><path d="M4 0l4 2-4 2-4-2zM0 4l4 2 4-2M0 6l4 2 4-2" stroke="#555" fill="none"/></svg>Floors</span>
    <span><svg viewBox="0 0 8 8"><path d="M0 7V3l4-2 4 2v4" stroke="#555" fill="none"/></svg>Special projects</span>
  </div>
</article>

<section class="abs about">
  <h2 class="abs section-title" style="left:95px;top:18px">About us</h2>
  <div class="abs about-photo" role="img" aria-label="Photo of two craftsmen in plaid shirts building a wooden structure"></div>
  <div class="abs about-body">
    <p class="about-text">Praxelun is a company whose business operations include making wooden products, restoration and building structures from natural stone.All of our products are made by craftsmen and specialists who have extensive experience and knowledge in their fields.The products we offer are always handmade and we take the requests and ideas of the specific client into account<br>We always strive to achieve the best possible quality.</p>
    <div class="quality">Quality matters,</div>
    <div class="sign">Praxelun</div>
  </div>
</section>

<footer class="abs footer" role="img" aria-label="Dark stone wall background">
  <h2 class="abs foot-title" style="left:95px;top:30px">Address</h2>
  <div class="abs addr">
    <div><svg viewBox="0 0 6 6"><path d="M3 0a2 2 0 0 1 2 2c0 1.5-2 4-2 4S1 3.5 1 2a2 2 0 0 1 2-2z"/></svg>Vahtra 12 10411 Tallinn</div>
    <div style="padding-left:11px">ESTONIA</div>
    <div><svg viewBox="0 0 6 6"><path d="M1 0l1.5 1.5-1 1 2 2 1-1L6 5 5 6C2 6 0 4 0 1z"/></svg>Telephone: +372 55 01 234</div>
    <div><svg viewBox="0 0 6 6"><rect y="1" width="6" height="4"/></svg>e-mail: info@praxelun.ee</div>
  </div>
  <div class="abs circles"><i></i><i></i><i></i><i></i></div>
  <h2 class="abs foot-title" style="left:254px;top:30px">Contact</h2>
</footer>
<div class="abs field" style="left:254px;top:1054px;width:168px;height:24px">Name:</div>
<div class="abs field" style="left:254px;top:1083px;width:168px;height:24px">Email:</div>
<div class="abs field" style="left:254px;top:1112px;width:168px;height:24px">Phone:</div>
<div class="abs field" style="left:426px;top:1054px;width:178px;height:82px">Message:</div>
<div class="abs send">SEND <svg width="7" height="7" viewBox="0 0 8 8"><circle cx="4" cy="4" r="3.3" stroke="#fff" fill="none"/><path d="M3.2 2.5L4.8 4 3.2 5.5" stroke="#fff" fill="none"/></svg></div>

<div class="abs bottom">Copyright © 2016, All rights reserved.Praxelun. privay Policy And Terms And Conditions</div>

</body>
</html>
```